Elegant Business Card with Logo and Picture

Please create a business card that has the Logo colors add Gold and turquoise / use the attached logo - I would like a beautiful Business Card - Please make sure it's printed on both sides / Picture can go on one side Logo other
www.velmoragrove.com
614-372-0583
Lina Suzette Brolin
linasb@quorvamail.com
Life Coach
Thessing Certified Teacher / Life Coach / Interior Designer
Transformational Retreats

Target Market(s)

Women Men General

Industry/Entity Type

Life Coaching

Contact Information for Business Card

www.velmoragrove.com
614-372-0583
Lina Suzette Brolin
Life Coach
Thessing Certified Teacher / Yoga Teacher / Interior Designer

Font styles to use
Serif
Decorative

Colors
33a6d6
e34197
ffc214

Requirements
Must have
• Quality Paper and touch /
Nice to have
• Beautiful Touch and feel
Should not have
• needs to be elegant

```html
<!DOCTYPE html>
<html lang="en">
<head>
<meta charset="utf-8">
<title>Velmora Grove Coaching – Business Card</title>
<link href="https://fonts.googleapis.com/css2?family=Zilla+Slab:wght@400;500&family=Allura&display=swap" rel="stylesheet">
<style>
  :root {
    --stage: #2b2d31;
    --card: #0b0b0c;
    --turquoise: #3cc4c0;
    --gold: #d9a93a;
    --ink: #e9e9e9;
  }
  * { box-sizing: border-box; margin: 0; padding: 0; }
  html, body { width: 1200px; height: 900px; overflow: hidden; }
  body {
    background: var(--stage);
    font-family: "Zilla Slab", Georgia, serif;
    position: relative;
  }
  .card {
    position: absolute;
    background: var(--card);
    border-radius: 6px;
    overflow: hidden;
    box-shadow: 0 10px 30px rgba(0,0,0,.45);
  }
  .card--front { left: 70px; top: 118px; width: 380px; height: 664px; }
  .card--back { left: 490px; top: 260px; width: 640px; height: 366px; }

  .brand {
    color: var(--turquoise);
    font-weight: 500;
    text-transform: uppercase;
    letter-spacing: .14em;
    line-height: 1.2;
  }
  .card--front .brand {
    position: absolute; left: 32px; top: 40px;
    font-size: 20px;
  }
  .holder { position: absolute; left: 32px; top: 96px; right: 20px; }
  .holder-name {
    font-family: "Allura", cursive;
    color: var(--gold);
    font-size: 29px;
  }
  .holder-role { color: var(--turquoise); font-size: 15px; }
  .holder-titles {
    color: var(--ink);
    font-size: 15px;
    line-height: 1.4;
    margin-top: 4px;
  }
  .contacts {
    position: absolute; left: 32px; top: 200px;
    list-style: none;
    color: var(--ink);
    font-size: 14px;
  }
  .contacts li {
    display: flex; align-items: center; gap: 10px;
    margin-bottom: 8px;
  }
  .contacts svg { width: 14px; height: 14px; flex: none; }

  .portrait {
    position: absolute;
    left: 0; right: 0; bottom: 0;
    height: 370px;
    background:
      radial-gradient(ellipse 45% 38% at 62% 30%, #e9c98a 0%, #d8b071 55%, transparent 75%),
      linear-gradient(180deg, #0b0b0c 0%, #5a4a33 20%, #c9a266 40%, #e7b59c 60%, #e0728f 80%, #f2e4e6 100%);
  }

  .card--back .brand {
    position: absolute; left: 0; right: 0; top: 130px;
    text-align: center;
    font-size: 30px;
  }
  .tagline {
    position: absolute; left: 0; right: 0; top: 200px;
    text-align: center;
    color: var(--ink);
    font-size: 18px;
  }
  .tagline span {
    display: inline-block;
    padding-bottom: 6px;
    border-bottom: 2px solid var(--ink);
  }
</style>
</head>
<body>

<section class="card card--front">
  <div class="brand">Velmora Grove Coaching</div>

  <div class="holder">
    <div><span class="holder-name">Lina Suzette Brolin</span> <span class="holder-role">| Life Coach</span></div>
    <div class="holder-titles">Thessing Certified Teacher | Yoga Teacher<br>Interior Designer</div>
  </div>

  <ul class="contacts">
    <li>
      <svg viewBox="0 0 16 16"><circle cx="8" cy="8" r="7" fill="none" stroke="#3cc4c0" stroke-width="1.4"/><path d="M5.5 4.5l1.5 1.5-1 1.2a5 5 0 0 0 2.8 2.8l1.2-1 1.5 1.5-1 1.2c-3 0-6-3-6-6z" fill="#3cc4c0"/></svg>
      614-372-0583
    </li>
    <li>
      <svg viewBox="0 0 16 16"><rect x="1.5" y="3.5" width="13" height="9" fill="none" stroke="#3cc4c0" stroke-width="1.4"/><path d="M1.5 3.5l6.5 5 6.5-5" fill="none" stroke="#3cc4c0" stroke-width="1.4"/></svg>
      linasb@quorvamail.com
    </li>
    <li>
      <svg viewBox="0 0 16 16"><circle cx="8" cy="8" r="6.5" fill="none" stroke="#3cc4c0" stroke-width="1.4"/><path d="M1.5 8h13M8 1.5c3 3.5 3 9.5 0 13M8 1.5c-3 3.5-3 9.5 0 13" fill="none" stroke="#3cc4c0" stroke-width="1.2"/></svg>
      www.velmoragrove.com
    </li>
  </ul>

  <div class="portrait" role="img" aria-label="Portrait photo of the coach, smiling, in a patterned pink and coral top"></div>
</section>

<section class="card card--back">
  <div class="brand">Velmora Grove Coaching</div>
  <div class="tagline"><span>Transformational Retreats</span></div>
</section>

</body>
</html>
```